Business card for law firm

Need business card for new law firm. Think confident, authoritative, conservative, but not stuffy or old-fashioned.

Contact Information for Business Card

Content for card - logo (uploaded), plus the following:

Paul Whitcombe (larger font)
Managing Partner (larger font, but not as large as name)
Level 9, 7 Ferris Lane
Sydney NSW 2000
Main Tel 02 9364 2710
Direct Tel 02 8472 3159
Email paul@qvlegal.com.au
www.qvlegal.com.au

Letterhead design should include logo plus:
Level 9, 7 Ferris Lane
Sydney NSW 2000
Tel 02 8472 3159
www.qvlegal.com.au

```html
<!DOCTYPE html>
<html lang="en">
<head>
<meta charset="utf-8">
<title>Quayvale Lawyers – Business Card</title>
<link rel="stylesheet" href="https://fonts.googleapis.com/css2?family=Cinzel:wght@400;500&family=Open+Sans:wght@400;600&display=swap">
<style>
  :root {
    --backdrop: #e9e4dc;
    --card-light: #d2ab85;
    --card-dark: #b98a5f;
    --ink: #1b1612;
    --rule: #8e6c4c;
    --navy: #0f2163;
  }
  html, body {
    margin: 0;
    padding: 0;
    width: 1200px;
    height: 900px;
    overflow: hidden;
    background: var(--backdrop);
  }
  .canvas {
    position: relative;
    width: 1200px;
    height: 900px;
  }
  .card {
    position: absolute;
    left: 330px;
    width: 556px;
    height: 343px;
    background: radial-gradient(ellipse at 30% 10%, var(--card-light) 0%, var(--card-dark) 100%);
    color: var(--ink);
    text-align: center;
    box-shadow: 2px 3px 6px rgba(0,0,0,0.25);
  }
  .card--back { top: 90px; }
  .card--front { top: 470px; }

  .contact-name {
    position: absolute;
    top: 70px;
    left: 0; right: 0;
    font-family: "Cinzel", serif;
    font-weight: 500;
    font-size: 22px;
    letter-spacing: 0.5px;
    line-height: 24px;
  }
  .contact-role {
    position: absolute;
    top: 93px;
    left: 0; right: 0;
    font-family: "Open Sans", sans-serif;
    font-size: 16px;
    line-height: 20px;
  }
  .rule {
    position: absolute;
    left: 200px;
    width: 156px;
    height: 1px;
    background: var(--rule);
  }
  .rule--upper { top: 120px; }
  .rule--lower { top: 220px; }
  .contact-list, .address {
    position: absolute;
    left: 0; right: 0;
    margin: 0;
    padding: 0;
    list-style: none;
    font-family: "Open Sans", sans-serif;
    font-size: 15.5px;
    line-height: 20.5px;
  }
  .contact-list { top: 128px; }
  .address { top: 229px; font-style: normal; }
  .contact-list .label { font-weight: 600; }
  .contact-list .note { font-size: 13px; }

  .brand-square {
    position: absolute;
    top: 70px;
    left: 246px;
    width: 76px;
    height: 76px;
    background: var(--navy);
  }
  .brand-name {
    position: absolute;
    top: 193px;
    left: 0; right: 0;
    font-family: "Cinzel", serif;
    font-weight: 400;
    color: var(--ink);
  }
  .brand-name .primary {
    display: block;
    font-size: 46px;
    line-height: 52px;
    letter-spacing: 1px;
  }
  .brand-name .secondary {
    display: block;
    font-size: 19px;
    line-height: 24px;
    letter-spacing: 13px;
    margin-left: 13px;
  }
</style>
</head>
<body>
<main class="canvas">
  <section class="card card--back" aria-label="Card back with contact details">
    <div class="contact-name">PAUL WHITCOMBE</div>
    <div class="contact-role">Managing Partner</div>
    <div class="rule rule--upper"></div>
    <ul class="contact-list">
      <li><span class="label">P:</span> 02 9364 2710</li>
      <li><span class="label">P:</span> 02 8472 3159 <span class="note">(DIRECT)</span></li>
      <li><span class="label">E:</span> paul@qvlegal.com.au</li>
      <li>www.qvlegal.com.au</li>
    </ul>
    <div class="rule rule--lower"></div>
    <address class="address">Level 9, 7 Ferris Lane<br>Sydney NSW 2000</address>
  </section>

  <section class="card card--front" aria-label="Card front with firm name">
    <div class="brand-square"></div>
    <div class="brand-name">
      <span class="primary">QUAYVALE</span>
      <span class="secondary">LAWYERS</span>
    </div>
  </section>
</main>
</body>
</html>
```